Company Website Re-design for Software development consultancy

We would like our company website to be redesigned using our existing marketing collateral and website content as a guide

current site : www.brightkestrel.com.au

For the different pages types and content please base on the following site : https://www.quorvalabs.net/

We want a coded site - but will replace the content ourselves within the sections you provide to customise to our needs.

Target Market(s)

Medium to Large corporates needing software design and development services

Industry/Entity Type

Information Technology

Coding

Coded - Design and coding required

Number of Pages Required

5+ page

Font styles to use
Sans Serif

Colors
ec1f27
ffffff
000000

Requirements
Must have
• Align to colour scheme of existing collateral
• Include pages for the key areas of our busines - see : https://www.quorvalabs.net/
Nice to have
• image rotators - make the site interesting to the business visitor

```html
<!DOCTYPE html>
<html lang="en">
<head>
<meta charset="utf-8">
<title>Bright Kestrel – Building Software Better</title>
<link rel="stylesheet" href="https://fonts.googleapis.com/css2?family=Montserrat:wght@400;600;800&family=Open+Sans:wght@400;600&display=swap">
<style>
:root{
  --red:#ec1f27;
  --black:#000000;
  --white:#ffffff;
  --ink:#333333;
  --muted:#555555;
  --grey-bg:#f2f2f2;
  --line:#e3e3e3;
  --footer:#2b2b2b;
  --footer-text:#cfcfcf;
}
*{box-sizing:border-box;margin:0;padding:0}
html,body{width:1200px;height:3888px;overflow:hidden;background:var(--white)}
body{font-family:"Open Sans",Arial,sans-serif;color:var(--ink);font-size:14px}
h1,h2,h3,.brand,.nav{font-family:"Montserrat",Arial,sans-serif}
section{position:relative;width:1200px}
.wrap{width:934px;margin:0 auto}
.section-title{color:var(--red);font-weight:400;font-size:34px;text-align:center;line-height:1.2}
.section-sub{text-align:center;color:var(--muted);font-size:16px;margin-top:8px}

/* header */
.site-header{height:72px;display:flex;align-items:center;justify-content:space-between;padding:0 133px}
.brand{font-weight:800;font-size:30px;letter-spacing:-0.5px;color:var(--black)}
.nav{display:flex;align-items:center;gap:38px;font-size:15px}
.nav a{color:var(--ink);text-decoration:none}
.nav a.active{color:var(--red)}
.nav a.cta{background:var(--red);color:var(--white);padding:8px 12px;border-radius:2px}

/* hero */
.hero{height:543px;display:flex;align-items:center;justify-content:center;
  background:linear-gradient(120deg,#0a1a4a 0%,#15357a 35%,#2a63b8 60%,#4a9be0 80%,#102a66 100%)}
.hero h1{color:var(--white);font-weight:400;font-size:46px}
.hero-arrow{position:absolute;top:328px;width:24px;height:24px;background:#111;display:flex;align-items:center;justify-content:center}
.hero-arrow.left{left:0}.hero-arrow.right{right:0}

/* welcome */
.welcome{height:260px;padding-top:72px}
.welcome p{width:934px;margin:22px auto 0;text-align:center;font-size:12.5px;line-height:1.9;color:var(--ink)}

/* faces */
.faces{height:465px;background:var(--grey-bg);padding-top:70px}
.face-cards{display:flex;justify-content:space-between;margin-top:32px}
.face-card{width:295px;height:223px;background:var(--white);border:1.5px solid var(--red);text-align:center;padding:20px 22px 0}
.face-card svg{display:block;margin:0 auto}
.face-card h3{color:var(--red);font-weight:400;font-size:20px;margin-top:22px}
.face-card p{font-size:11px;line-height:1.6;margin-top:8px;color:var(--ink)}

/* team */
.team{height:500px;padding-top:72px}
.team .intro{text-align:center;font-size:12.5px;line-height:1.8;margin-top:20px}
.team-grid{display:flex;justify-content:space-between;width:800px;margin:26px auto 0}
.member{width:260px;text-align:center}
.portrait{width:125px;height:123px;margin:0 auto;background:linear-gradient(160deg,#8a9aa8,#4b5560)}
.member h3{color:var(--red);font-weight:400;font-size:19px;margin-top:12px}
.member .role{font-size:12px;letter-spacing:.5px;margin-top:4px}
.member .bio{font-size:10.5px;margin-top:6px;color:var(--muted)}
.social-sq{width:14px;height:14px;background:#222;margin:16px auto 0;border-radius:2px}

/* products */
.products{height:970px;background:var(--grey-bg);padding-top:80px}
.product-row{display:flex;justify-content:space-between;align-items:center;margin-top:38px}
.feature-list{list-style:none;width:300px}
.feature-list li{display:flex;gap:14px;font-size:17px;line-height:1.45;color:var(--black);margin-bottom:26px}
.feature-list svg{flex:none;margin-top:3px}
.product-visual{width:606px;height:405px;background:linear-gradient(135deg,#dfe6df 0%,#c9d3cc 40%,#2c2c2c 60%,#6f6f72 100%)}
.start-box{margin-top:60px;height:243px;background:var(--white);border:1px solid var(--line);padding-top:50px;text-align:center}
.start-box h3{color:var(--red);font-weight:400;font-size:19px}
.steps{display:flex;justify-content:space-around;margin-top:30px}
.step{width:280px;font-size:12.5px}
.step svg{display:block;margin:0 auto 8px}
.step .link{color:var(--red);font-size:19px;margin-top:4px}

/* blog */
.blog{height:743px;padding-top:80px}
.blog-cards{display:flex;justify-content:space-between;margin-top:28px}
.post{width:439px;background:var(--grey-bg);height:490px}
.post-image{height:255px}
.post-image.one{background:linear-gradient(135deg,#041a3a,#0a5a8a 55%,#19c0d8)}
.post-image.two{background:linear-gradient(160deg,#02122e,#123f8a 55%,#2d7ad0)}
.post-body{padding:32px 24px 0}
.post h3{font-family:"Open Sans",Arial,sans-serif;font-weight:600;font-size:16px;line-height:1.4;color:var(--black)}
.post p{font-size:10px;line-height:1.7;color:var(--muted);margin-top:12px}
.btn-more{display:inline-block;margin-top:20px;border:1px solid #bbb;padding:9px 20px;font-size:11px;color:var(--muted);background:var(--white)}
.blog-arrow{position:absolute;top:3230px}
.blog-arrow{top:430px}
.blog-arrow.left{left:48px}.blog-arrow.right{right:48px}

/* contact */
.contact{height:159px;background:var(--grey-bg);padding-top:68px}
.contact-row{display:flex;justify-content:space-between;width:860px;margin:18px auto 0;font-size:15px;color:var(--ink)}
.contact-row span{display:flex;align-items:center;gap:8px}

/* footer */
.site-footer{height:176px;background:var(--footer);color:var(--footer-text);padding:40px 133px 0;position:relative;font-size:11px}
.footer-links{display:flex;gap:10px}
.footer-links span.sep{color:#777}
.copy{margin-top:18px}
.footer-social{position:absolute;right:133px;top:90px;display:flex;gap:22px}
.footer-social i{width:14px;height:14px;border-radius:50%;background:var(--footer-text);display:block}
</style>
</head>
<body>

<header class="site-header">
  <div class="brand">BRIGHT KESTREL</div>
  <nav class="nav">
    <a class="active">Home</a><a>About Us</a><a>Services</a><a>Blog</a><a class="cta">Contact Us</a>
  </nav>
</header>

<section class="hero" role="img" aria-label="Hero photo: close-up of glowing program code on a blue screen">
  <div class="hero-arrow left"><svg width="10" height="10" viewBox="0 0 10 10"><path d="M7 1 3 5l4 4" fill="none" stroke="#fff" stroke-width="2"/></svg></div>
  <h1>Building Software Better</h1>
  <div class="hero-arrow right"><svg width="10" height="10" viewBox="0 0 10 10"><path d="M3 1l4 4-4 4" fill="none" stroke="#fff" stroke-width="2"/></svg></div>
</section>

<section class="welcome">
  <h2 class="section-title">Welcome to Bright Kestrel</h2>
  <p>After spending more than twenty years each in the industry, including seven years in New York building electronic trading systems for Harlow Grant – the founders realised that there was a distinct lack in the market of people focusing on how software is developed – not just solving the business problem, but automating the development itself to increase both productivity and quality.</p>
</section>

<section class="faces">
  <div class="wrap">
    <h2 class="section-title">The Three Faces of Bright Kestrel</h2>
    <p class="section-sub">We are all about building software better.</p>
    <div class="face-cards">
      <div class="face-card">
        <svg width="64" height="64" viewBox="0 0 64 64" fill="none" stroke="#222" stroke-width="2"><rect x="20" y="4" width="24" height="14"/><path d="M32 18v10M10 28h44M10 28v8M32 28v8M54 28v8"/><rect x="2" y="36" width="16" height="12"/><rect x="24" y="36" width="16" height="12"/><rect x="46" y="36" width="16" height="12"/><path d="M4 56h56"/></svg>
        <h3>Consulting</h3>
        <p>Up-skill your team by using our consultants - for either short or long term engagements.</p>
      </div>
      <div class="face-card">
        <svg width="64" height="64" viewBox="0 0 64 64" fill="none" stroke="#222" stroke-width="2"><path d="M6 6h22v8a4 4 0 0 1 0 8v6H6zM36 6h22v22h-8a4 4 0 0 0-8 0h-6zM6 36h8a4 4 0 0 1 8 0h6v22H6zM36 36h22v22H36v-8a4 4 0 0 0 0-8z"/></svg>
        <h3>Projects</h3>
        <p>We can deliver a large project on a fixed price basis at a quality standard you won't believe.</p>
      </div>
      <div class="face-card">
        <svg width="64" height="64" viewBox="0 0 64 64" fill="none" stroke="#222" stroke-width="2"><path d="M8 30h10v28H8zM18 32l10-14 2-12c4 0 6 4 5 10l-2 8h18c4 0 5 4 3 6 2 2 1 5-1 6 2 2 1 5-2 6 1 3-1 6-5 6H18"/><path d="M30 2v-0M44 4l-3 5M52 12l-5 3M20 4l3 5"/></svg>
        <h3>Quillsheet</h3>
        <p>Our product, Quillsheet, allows you to skip the development cycle and turn an existing spreadsheet directly into either a web service or a web site</p>
      </div>
    </div>
  </div>
</section>

<section class="team">
  <div class="wrap">
    <h2 class="section-title">Meet our leadership team</h2>
    <p class="intro">Between just the partners, we have more than 60 years of software development experience. We combine a solid knowledge of computer science with a practical, pragmatic approach to delivering software.</p>
  </div>
  <div class="team-grid">
    <div class="member"><div class="portrait" role="img" aria-label="Portrait photo of Miles Harrow"></div><h3>Miles Harrow</h3><div class="role">PARTNER</div><div class="bio">Miles is one of the best developers on the planet</div><div class="social-sq"></div></div>
    <div class="member"><div class="portrait" role="img" aria-label="Portrait photo of Owen Pell"></div><h3>Owen Pell</h3><div class="role">PARTNER</div><div class="bio">Owen's been running software projects for 20 years</div><div class="social-sq"></div></div>
    <div class="member"><div class="portrait" role="img" aria-label="Portrait photo of Tobias Reyne"></div><h3>Tobias Reyne</h3><div class="role">PARTNER</div><div class="bio">Tobias codes for fun as much as he does for work</div><div class="social-sq"></div></div>
  </div>
</section>

<section class="products">
  <div class="wrap">
    <h2 class="section-title">Our Products</h2>
    <p class="section-sub">Mauris pulvinar volutpat ipsum, nec sodales arcu dignissim sed.</p>
    <div class="product-row">
      <ul class="feature-list">
        <li><svg width="16" height="16" viewBox="0 0 16 16"><circle cx="8" cy="8" r="8" fill="#111"/><path d="M4 8l3 3 5-6" fill="none" stroke="#fff" stroke-width="2"/></svg>Manage subscriptions to your models via an interactive web portal.</li>
        <li><svg width="16" height="16" viewBox="0 0 16 16"><circle cx="8" cy="8" r="8" fill="#111"/><path d="M4 8l3 3 5-6" fill="none" stroke="#fff" stroke-width="2"/></svg>Track usage of your models and associate with a pricing model.</li>
        <li><svg width="16" height="16" viewBox="0 0 16 16"><circle cx="8" cy="8" r="8" fill="#111"/><path d="M4 8l3 3 5-6" fill="none" stroke="#fff" stroke-width="2"/></svg>Publish with one-click using our Spreadsheet Add-in.</li>
        <li><svg width="16" height="16" viewBox="0 0 16 16"><circle cx="8" cy="8" r="8" fill="#111"/><path d="M4 8l3 3 5-6" fill="none" stroke="#fff" stroke-width="2"/></svg>Calculation logic in Spreadsheet is automatically converted into an industry-standard web service.</li>
      </ul>
      <div class="product-visual" role="img" aria-label="Product screenshots: a spreadsheet calculator and a laptop showing the Quillsheet dashboard, with the product badge"></div>
    </div>
    <div class="start-box">
      <h3>Get Started</h3>
      <div class="steps">
        <div class="step"><svg width="24" height="24" viewBox="0 0 24 24" fill="none" stroke="#222" stroke-width="2"><circle cx="12" cy="12" r="10"/><path d="M2 12h20M12 2c3 3 3 17 0 20M12 2c-3 3-3 17 0 20"/></svg>Create an account at<div class="link">http://quillsheet.today</div></div>
        <div class="step"><svg width="24" height="24" viewBox="0 0 24 24"><path d="M12 2v12M7 9l5 5 5-5" fill="none" stroke="#222" stroke-width="2.5"/><rect x="2" y="17" width="20" height="5" fill="#222"/></svg>Download and Install the Quillsheet Add-in for<div class="link">Spreadsheet</div></div>
        <div class="step"><svg width="28" height="24" viewBox="0 0 28 24"><path d="M7 20a6 6 0 0 1 0-12 8 8 0 0 1 15 2 5 5 0 0 1-1 10z" fill="#222"/><path d="M14 18v-7M11 14l3-3 3 3" fill="none" stroke="#fff" stroke-width="2"/></svg>Build you model and publish to our<div class="link">Cloud Services</div></div>
      </div>
    </div>
  </div>
</section>

<section class="blog">
  <div class="wrap">
    <h2 class="section-title">Blog</h2>
    <p class="section-sub">Mauris pulvinar volutpat ipsum, nec sodales arcu dignissim</p>
    <div class="blog-cards">
      <article class="post">
        <div class="post-image one" role="img" aria-label="Illustration of a laptop on a glowing circuit board"></div>
        <div class="post-body">
          <h3>Vestibulum id scelerisque turpis, at vulputate neque. Mauris molestie vitae orci sed condimentum</h3>
          <p>Vivamus tempus quam et risus fringilla dignissim. Etiam rutrum justo cursus dolor laoreet, eu gravida leo ullamcorper. Pellentesque magna orci, placerat at nisl at, porta ultrices turpis. Fusce in eros non orci posuere viverra.</p>
          <span class="btn-more">Read more</span>
        </div>
      </article>
      <article class="post">
        <div class="post-image two" role="img" aria-label="Photo of colourful code on a dark monitor"></div>
        <div class="post-body">
          <h3>Integer sapien felis, sodales ut lacus non, dignissim pretium nibh</h3>
          <p>Nulla cursus ac sapien eget porttitor. Pellentesque accumsan ut metus sed elementum. Integer ac ante neque. Vestibulum a eleifend sapien, at consectetur risus. Nulla finibus lacinia dolor, semper dictum leo eleifend non.</p>
          <span class="btn-more">Read more</span>
        </div>
      </article>
    </div>
  </div>
  <svg class="blog-arrow left" width="14" height="24" viewBox="0 0 14 24"><path d="M12 2 2 12l10 10" fill="none" stroke="#999" stroke-width="2"/></svg>
  <svg class="blog-arrow right" width="14" height="24" viewBox="0 0 14 24"><path d="M2 2l10 10L2 22" fill="none" stroke="#999" stroke-width="2"/></svg>
</section>

<section class="contact">
  <h2 class="section-title">Contact Info</h2>
  <div class="contact-row">
    <span><svg width="12" height="16" viewBox="0 0 12 16"><path d="M6 0a6 6 0 0 1 6 6c0 4-6 10-6 10S0 10 0 6a6 6 0 0 1 6-6z" fill="#333"/><circle cx="6" cy="6" r="2" fill="#f2f2f2"/></svg>42 - 44 Lantern Lane, Sydney 2000</span>
    <span><svg width="14" height="14" viewBox="0 0 14 14"><path d="M3 0l3 3-2 2c1 2 3 4 5 5l2-2 3 3-2 3C6 14 0 8 0 2z" fill="#333"/></svg>465 555 0192</span>
    <span><svg width="16" height="12" viewBox="0 0 16 12"><rect width="16" height="12" fill="#333"/><path d="M0 0l8 6 8-6" fill="none" stroke="#f2f2f2" stroke-width="1.5"/></svg>info@brightkestrel.com.au</span>
  </div>
</section>

<footer class="site-footer">
  <div class="footer-links"><span>Home</span><span class="sep">|</span><span>About Us</span><span class="sep">|</span><span>Services</span><span class="sep">|</span><span>Blog</span><span class="sep">|</span><span>Contact Us</span></div>
  <div class="copy">Copyright © 2018 Bright Kestrel. All rights reserved.</div>
  <div class="footer-social"><i></i><i></i></div>
</footer>

</body>
</html>
```